Letterhead and matching envelope design for a dental office

We need a new stationary design, letterhead and envelope #10, for a dental office in Denver area. We are called Bright Harbor Dental. We want a simple and minimalistic design but not a boring design. I wish to have one good point that makes it look professional. I have attached our logo. Feel free to use either one. I want the design for letterhead and envelope look like a "matching pair" but not look the same. The envelope doesn't have to be white and it will have an address window on bottom left.

Target Market(s)

everyone who visits dentist (adults)

Industry/Entity Type

Dental

Font styles to use
Other font styles liked:
• close to font on logo or something that matches well

Requirements
Must have
• professional
• simple, minimalistic
• unique point that stands out
Nice to have
• matching but not same design for letterhead and envelope
Should not have
• not look like all the other boring designs
• no flowery, distracting feats

```html
<!DOCTYPE html>
<html lang="en">
<head>
<meta charset="utf-8">
<title>Bright Harbor Dental – Letterhead</title>
<link href="https://fonts.googleapis.com/css2?family=Open+Sans:wght@400;600&display=swap" rel="stylesheet">
<style>
  :root {
    --brand-green: #43b649;
    --ink: #3a3a3a;
    --paper: #ffffff;
    --backdrop: #e6e6e6;
  }
  * { margin: 0; padding: 0; box-sizing: border-box; }
  html, body {
    width: 1200px;
    height: 1200px;
    overflow: hidden;
    background: var(--backdrop);
    font-family: "Open Sans", Arial, sans-serif;
  }
  .letterhead {
    position: absolute;
    left: 175px;
    top: 50px;
    width: 850px;
    height: 1100px;
    background: var(--paper);
    overflow: hidden;
    box-shadow: 0 2px 10px rgba(0,0,0,0.08);
  }
  .brand {
    position: absolute;
    left: 70px;
    top: 70px;
    display: flex;
    align-items: center;
    gap: 12px;
  }
  .brand-dot {
    width: 18px;
    height: 18px;
    border-radius: 50%;
    background: var(--brand-green);
  }
  .brand-name {
    font-weight: 600;
    font-size: 26px;
    letter-spacing: 2px;
    color: var(--brand-green);
    text-transform: uppercase;
  }
  .contact {
    position: absolute;
    right: 70px;
    top: 66px;
    font-size: 12.5px;
    line-height: 1.45;
    color: var(--ink);
  }
  .contact-name {
    color: var(--brand-green);
    font-weight: 600;
    text-transform: uppercase;
  }
  .contact-address { margin-bottom: 6px; }
  .contact-line {
    display: flex;
    align-items: center;
    gap: 7px;
  }
  .contact-line svg { width: 11px; height: 11px; flex: none; }
  .swoosh {
    position: absolute;
    left: 0;
    bottom: 0;
    width: 850px;
    height: 1100px;
  }
</style>
</head>
<body>
  <main class="letterhead">
    <div class="brand">
      <span class="brand-dot"></span>
      <span class="brand-name">Bright Harbor Dental</span>
    </div>

    <address class="contact" style="font-style:normal">
      <div class="contact-name">Bright Harbor Dental</div>
      <div class="contact-address">4218 Larkspur Ave Suite 210<br>Aurora, CO 80014</div>
      <div class="contact-line">
        <svg viewBox="0 0 12 12" aria-hidden="true"><path fill="#43b649" d="M2.5 1h2l1 3-1.3 1a7 7 0 0 0 2.8 2.8l1-1.3 3 1v2a1.5 1.5 0 0 1-1.5 1.5A9.5 9.5 0 0 1 1 2.5 1.5 1.5 0 0 1 2.5 1z"/></svg>
        <span>720-555-0142</span>
      </div>
      <div class="contact-line">
        <svg viewBox="0 0 12 12" aria-hidden="true"><rect x="0.5" y="2" width="11" height="8" rx="1" fill="#43b649"/><path d="M1 3l5 3.5L11 3" stroke="#fff" stroke-width="1" fill="none"/></svg>
        <span>hello@brightharbordental.com</span>
      </div>
      <div class="contact-line">
        <svg viewBox="0 0 12 12" aria-hidden="true"><circle cx="6" cy="6" r="5" fill="none" stroke="#43b649" stroke-width="1.2"/><ellipse cx="6" cy="6" rx="2.2" ry="5" fill="none" stroke="#43b649" stroke-width="1"/><path d="M1 6h10" stroke="#43b649" stroke-width="1"/></svg>
        <span>www.brightharbordental.com</span>
      </div>
    </address>

    <svg class="swoosh" viewBox="0 0 850 1100" aria-hidden="true">
      <path fill="var(--brand-green)" d="M850 720 C800 880 640 1000 400 1100 L850 1100 Z"/>
      <path fill="var(--paper)" d="M420 1100 C560 1040 690 960 770 880 C700 965 580 1040 450 1100 Z"/>
    </svg>
  </main>
</body>
</html>
```